Homemaking training schools needs a Business Card design

Designer, Hello!

No special requirements, good-looking enough.
--------------------------------------------------------------------------

Name: Marcus Dole
Chairman
Tel: 0574-71948263
Mobile: 13857420916
Email: kelvora@mailnest.example
Web: www.prt2019.example
Add: No.258, LanpingJie, BeiyuanQu, Ningbo, Zhejiang

LOGO
Ningbo PRT Homemaking Training School

Target Market(s)

pregnant women, mothers, infants, the elderly and families, including cleaning, cooking, nursing training.

Industry/Entity Type

Business

Contact Information for Business Card

Name: Marcus Dole
Chairman
Tel: 0574-71948263
Mobile: 13857420916
Email: kelvora@mailnest.example
Web: www.prt2019.example

LOGO

Font styles to use
Serif
Sans Serif
Decorative

Requirements
Nice to have
• Feels: clean, specifications, safety, comfort, warmth and happiness.

```html
<!DOCTYPE html>
<html lang="en">
<head>
<meta charset="utf-8">
<title>PeiRunTang – Business Card</title>
<link href="https://fonts.googleapis.com/css2?family=Montserrat:wght@500;600;700;800&display=swap" rel="stylesheet">
<style>
  :root {
    --backdrop: #2b2b2d;
    --card: #050505;
    --accent-blue: #1e7fd0;
    --text-light: #ffffff;
  }
  * { box-sizing: border-box; margin: 0; padding: 0; }
  html, body {
    width: 1200px; height: 900px; overflow: hidden;
    background: var(--backdrop);
  }
  .stage { position: relative; width: 1200px; height: 900px; }

  .card {
    position: absolute;
    width: 700px; height: 400px;
    background: var(--card);
    box-shadow: 0 18px 40px rgba(0,0,0,.55);
    font-family: "Montserrat", sans-serif;
    color: var(--text-light);
    overflow: hidden;
  }
  .card--front { left: 60px; top: 40px; }
  .card--back  { left: 440px; top: 460px; }

  /* Company name placeholder */
  .company { position: absolute; display: flex; align-items: center; }
  .company__mark { flex: none; background: var(--accent-blue); }
  .company__name {
    font-family: "Montserrat", sans-serif;
    font-weight: 700;
    color: var(--text-light);
    line-height: 1;
    white-space: nowrap;
  }

  .card--front .company { left: 0; right: 0; top: 160px; justify-content: center; gap: 18px; }
  .card--front .company__mark { width: 34px; height: 34px; }
  .card--front .company__name { font-size: 54px; }

  .card--back .company { right: 40px; top: 62px; gap: 12px; }
  .card--back .company__mark { width: 22px; height: 22px; }
  .card--back .company__name { font-size: 36px; }

  .website-front {
    position: absolute; left: 40px; bottom: 36px;
    font-weight: 700; font-size: 21px; letter-spacing: .3px;
  }

  /* Name band */
  .name-band {
    position: absolute; left: 0; top: 238px;
    width: 330px; height: 72px;
    background: var(--accent-blue);
    padding: 11px 0 0 50px;
  }
  .name-band__name { font-weight: 800; font-size: 28px; letter-spacing: .5px; line-height: 1.05; }
  .name-band__title { font-weight: 600; font-size: 13px; letter-spacing: .8px; }

  /* Contact block */
  .contact {
    position: absolute; left: 400px; top: 170px;
    font-size: 15px; font-weight: 500; line-height: 1.45;
  }
  .contact__address { margin-bottom: 6px; }
  .contact__list { list-style: none; padding-left: 26px; }
  .contact__item { display: flex; align-items: center; gap: 10px; }
  .contact__icon { width: 13px; height: 13px; flex: none; fill: none; stroke: var(--accent-blue); stroke-width: 1.8; }
  .contact__item .contact__icon { margin-left: -23px; }
</style>
</head>
<body>
<main class="stage">

  <section class="card card--front" aria-label="Card front">
    <div class="company">
      <span class="company__mark"></span>
      <span class="company__name">PeiRunTang</span>
    </div>
    <p class="website-front">www.prt2019.example</p>
  </section>

  <section class="card card--back" aria-label="Card back">
    <div class="company">
      <span class="company__mark"></span>
      <span class="company__name">PeiRunTang</span>
    </div>

    <div class="name-band">
      <p class="name-band__name">MARCUS DOLE</p>
      <p class="name-band__title">CHAIRMAN</p>
    </div>

    <div class="contact">
      <p class="contact__address">258, LanpingJie<br>BeiyuanQu, Ningbo, Zhejiang</p>
      <ul class="contact__list">
        <li class="contact__item">
          <svg class="contact__icon" viewBox="0 0 16 16"><path d="M4 1.5l2.2 3-1.4 1.6c.8 1.9 2.2 3.4 4.1 4.2l1.6-1.4 3 2.2-1.3 2.6C6.5 13.5 2.5 9.5 1.4 3z"/></svg>
          <span>0574-71948263</span>
        </li>
        <li class="contact__item">
          <svg class="contact__icon" viewBox="0 0 16 16"><rect x="4" y="1" width="8" height="14" rx="1.5"/><line x1="7" y1="12.5" x2="9" y2="12.5"/></svg>
          <span>13857420916</span>
        </li>
        <li class="contact__item">
          <svg class="contact__icon" viewBox="0 0 16 16"><rect x="1.5" y="3.5" width="13" height="9" rx="1"/><path d="M1.5 4l6.5 5 6.5-5"/></svg>
          <span>kelvora@mailnest.example</span>
        </li>
        <li class="contact__item">
          <svg class="contact__icon" viewBox="0 0 16 16"><circle cx="8" cy="8" r="6.5"/><ellipse cx="8" cy="8" rx="2.8" ry="6.5"/><line x1="1.5" y1="8" x2="14.5" y2="8"/></svg>
          <span>www.prt2019.example</span>
        </li>
      </ul>
    </div>
  </section>

</main>
</body>
</html>
```